New business card/stationary for a consulting company

I am looking for a clean and very professional looking business card for my consulting company as well as corresponding stationary. I am uploading our logo. I like simple and powerful for the feel. No graphics but I am open on everything else. Below is my contact information but would like the final to be in a version I can add my employees information into and print. Thank you.

Daniel Whitcombe
dan@ferncliffadvisory.com
2870 North 9th Avenue, Summit Floor, Elm Ridge, Illinois 60531
www.ferncliffadvisory.com

Industry/Entity Type

Consulting

Contact Information for Business Card

Daniel Whitcombe
dan@ferncliffadvisory.com
www.ferncliffadvisory.com

Font styles to use
Serif
Sans Serif

Requirements
Must have
• Our logo and the business card details.
Nice to have
• our website www.ferncliffadvisory.com

```html
<!DOCTYPE html>
<html lang="en">
<head>
<meta charset="utf-8">
<title>Ferncliff Advisory — Letterhead</title>
<link rel="stylesheet" href="https://fonts.googleapis.com/css2?family=Cinzel:wght@500;600&family=Mulish:wght@400&display=swap">
<style>
  :root {
    --navy: #201d5f;
    --paper: #ffffff;
  }
  * { margin: 0; padding: 0; box-sizing: border-box; }
  html, body {
    width: 927px;
    height: 1200px;
    overflow: hidden;
    background: var(--paper);
  }
  .letterhead {
    position: relative;
    width: 927px;
    height: 1200px;
    background: var(--paper);
    color: var(--navy);
  }
  .brand-square {
    position: absolute;
    left: 433px;
    top: 40px;
    width: 61px;
    height: 61px;
    background: var(--navy);
  }
  .brand-name {
    position: absolute;
    left: 0;
    width: 927px;
    top: 116px;
    text-align: center;
    font-family: "Cinzel", serif;
    font-weight: 500;
    font-size: 33px;
    letter-spacing: 1px;
    line-height: 1;
    color: var(--navy);
  }
  .rule-heavy {
    position: absolute;
    left: 0;
    top: 179px;
    width: 927px;
    height: 2.5px;
    background: var(--navy);
  }
  .rule-light {
    position: absolute;
    left: 0;
    top: 191px;
    width: 927px;
    height: 1px;
    background: var(--navy);
  }
  .sender {
    position: absolute;
    right: 33px;
    top: 1072px;
    text-align: right;
  }
  .sender-name {
    font-family: "Cinzel", serif;
    font-weight: 600;
    font-size: 19px;
    letter-spacing: 1.6px;
    line-height: 22px;
    margin-bottom: 2px;
  }
  .sender-details {
    font-family: "Mulish", sans-serif;
    font-weight: 400;
    font-size: 13.5px;
    line-height: 17.6px;
    font-style: normal;
  }
</style>
</head>
<body>
  <main class="letterhead">
    <header>
      <div class="brand-square"></div>
      <h1 class="brand-name">FERNCLIFF ADVISORY</h1>
      <div class="rule-heavy"></div>
      <div class="rule-light"></div>
    </header>
    <footer class="sender">
      <p class="sender-name">Daniel Whitcombe</p>
      <address class="sender-details">
        dan@ferncliffadvisory.com<br>
        2870 North 9th Avenue, Summit Floor,<br>
        Elm Ridge, Illinois 60531<br>
        www.ferncliffadvisory.com
      </address>
    </footer>
  </main>
</body>
</html>
```